Business Broker Graphics Package

Hi,

Seeking a smart and professional graphics package design including business card design (double-sided) and letterhead and PowerPoint slide template.

3 Deliverables:

1. Company Letterhead
2. Business Card (two sided) (will consider one sided designs)
3. PowerPoint Template. Requires cover PPT and 2nd page design.

For the prototype use this info:
Marcus Dellorane RPA
Registered Practice Adviser
5678 Harlow Rd.
Larkfield, OH 44790
555.014.2273
Demo@Quillbrookpath.com
www.QuillbrookPath.com

I'll give exact information to winner to finalize later.

I've attached the logo..

Business card will be double sided and info for back of card is in attachment.

Look forward to your great ideas and concepts!

Target Market(s)

President's and business owners, CPA's and other professionals.

Industry/Entity Type

Business

Requirements
Nice to have
• Prefer horizontal card, but will consider vertical card design.

The business card should be all or primarily white. Text colors should be same as logo creative combination of black and forest green.

PowerPoint can be white background or lighter palette of colors I like gold color. I do not like darkly colored PowerPoint designs I prefer light and bright designs.

```html
<!DOCTYPE html>
<html lang="en">
<head>
<meta charset="utf-8">
<title>QuillbrookPath Stationery Package</title>
<link href="https://fonts.googleapis.com/css2?family=Cinzel:wght@500&family=Source+Sans+3:wght@400;600;700&family=Roboto:wght@400;500&display=swap" rel="stylesheet">
<style>
  :root {
    --forest: #0a3b25;
    --ink: #1a1a1a;
    --stage: #8c8c8c;
    --paper: #ffffff;
    --rule: #d9d9d9;
    --muted: #555555;
    --slide-rule: #6d8a7a;
  }
  * { margin: 0; padding: 0; box-sizing: border-box; }
  html, body { width: 1200px; height: 640px; overflow: hidden; }
  body { background: var(--stage); position: relative; font-family: "Source Sans 3", sans-serif; color: var(--ink); }

  .sheet { position: absolute; background: var(--paper); overflow: hidden; box-shadow: 0 2px 5px rgba(0,0,0,.35); }

  /* wordmark: company name set in the body typeface */
  .brand { font-family: "Source Sans 3", sans-serif; font-weight: 700; color: var(--forest); line-height: 1; white-space: nowrap; display: block; }

  /* letterhead */
  .letterhead { left: 18px; top: 14px; width: 478px; height: 616px; }
  .letterhead .brand { position: absolute; left: 0; right: 0; top: 62px; text-align: center; font-size: 26px; }
  .letter-body { position: absolute; left: 42px; width: 396px; font-size: 7.3px; line-height: 14px; }
  .recipient { top: 116px; }
  .recipient strong, .signatory strong { font-weight: 700; }
  .letter-text { top: 180px; }
  .letter-text p { margin-bottom: 14px; }
  .signature { position: absolute; left: 42px; top: 476px; width: 154px; height: 34px; background: linear-gradient(90deg, #f4f4f4, #ebebeb); }
  .signatory { top: 516px; }
  .footer-rule { position: absolute; left: 0; right: 0; top: 576px; height: 1.5px; background: var(--rule); }
  .footer-contact { position: absolute; left: 42px; top: 596px; font-size: 7.5px; color: var(--ink); }
  .footer-contact .sep { color: #999; margin: 0 4px; }
  .letterhead .ownership-tab { position: absolute; left: 282px; top: 591px; width: 196px; height: 25px; background: var(--forest); clip-path: polygon(8px 0, 100% 0, 100% 100%, 0 100%); color: #fff; font-family: "Cinzel", serif; font-size: 9px; letter-spacing: .3px; display: flex; align-items: center; justify-content: center; }

  /* slides */
  .slide-cover { left: 508px; top: 18px; width: 396px; height: 298px; background: var(--forest); }
  .slide-cover .cover-rule { position: absolute; left: 0; right: 0; top: 45px; height: 1.5px; background: var(--slide-rule); }
  .slide-cover .logo-band { position: absolute; left: 0; right: 0; top: 200px; height: 58px; background: var(--paper); display: flex; align-items: center; justify-content: center; }
  .slide-cover .brand { font-size: 18px; }
  .service-strip { position: absolute; left: 0; right: 0; color: #fff; text-align: center; }
  .service-strip .title { font-family: "Cinzel", serif; font-size: 8.5px; letter-spacing: .3px; display: block; }
  .service-strip .services { font-family: "Roboto", sans-serif; font-size: 7.6px; display: block; margin-top: 3px; }
  .slide-cover .service-strip { top: 265px; }
  .services span::before { content: "\25A0"; font-size: 5px; vertical-align: 2px; margin: 0 3px 0 5px; }

  .slide-content { left: 508px; top: 330px; width: 394px; height: 296px; }
  .slide-content .brand { position: absolute; left: 18px; top: 16px; font-size: 13px; }
  .slide-content .header-rule { position: absolute; left: 108px; right: 0; top: 40px; height: 1.2px; background: var(--rule); }
  .slide-content .base-band { position: absolute; left: 0; top: 284px; width: 232px; height: 12px; background: var(--ink); clip-path: polygon(0 0, 100% 0, 97% 100%, 0 100%); }
  .slide-content .contact-tab { position: absolute; left: 232px; top: 278px; width: 162px; height: 18px; background: var(--forest); clip-path: polygon(6px 0, 100% 0, 100% 100%, 0 100%); color: #fff; font-size: 5.6px; display: flex; align-items: center; justify-content: center; }
  .contact-tab .sep { margin: 0 3px; opacity: .7; }

  /* business cards */
  .card-front { left: 925px; top: 24px; width: 254px; height: 148px; }
  .card-front .brand { position: absolute; left: 15px; top: 44px; font-size: 13px; }
  .card-holder { position: absolute; right: 14px; top: 52px; text-align: right; font-family: "Roboto", sans-serif; }
  .card-holder .name { font-size: 9.6px; color: var(--ink); display: block; }
  .card-holder .role { font-size: 5.6px; color: var(--ink); display: block; margin-top: 4px; }
  .card-contacts { position: absolute; left: 15px; top: 78px; list-style: none; font-family: "Roboto", sans-serif; font-size: 6.4px; color: var(--muted); }
  .card-contacts li { display: flex; align-items: center; height: 11px; }
  .card-contacts svg { width: 7.5px; height: 7.5px; margin-right: 3px; flex: none; }
  .card-front .card-rule { position: absolute; left: 0; right: 0; top: 126px; height: 1.2px; background: var(--rule); }
  .card-front .ownership-tab { position: absolute; left: 147px; top: 134px; width: 107px; height: 14px; background: var(--forest); clip-path: polygon(5px 0, 100% 0, 100% 100%, 0 100%); color: #fff; font-family: "Cinzel", serif; font-size: 6.2px; display: flex; align-items: center; justify-content: center; }

  .card-back { left: 924px; top: 206px; width: 254px; height: 148px; }
  .card-back .brand { position: absolute; left: 14px; top: 10px; writing-mode: vertical-rl; font-size: 11px; }
  .card-back .service-strip { top: 106px; height: 42px; background: var(--forest); padding-top: 7px; }
  .card-back .service-strip .title { font-size: 8px; }
  .card-back .service-strip .services { font-size: 6.4px; }
</style>
</head>
<body>

<section class="sheet letterhead" aria-label="Company letterhead">
  <span class="brand">QuillbrookPath</span>

  <div class="letter-body recipient">
    To<br>
    <strong>The Lorem Ipsum</strong><br>
    Sample text for printing and typesetting industry
  </div>

  <div class="letter-body letter-text">
    <p>Lorem Ipsum is simply dummy text of the printing and typesetting industry. Lorem Ipsum has been the industry's standard dummy text ever since the 1500s, when an unknown printer took a galley of type and scrambled it to make a type specimen book. It has survived not only five centuries, but also the leap into electronic typesetting, remaining essentially unchanged. It was popularised in the 1960s with the release of Letraset sheets containing Lorem Ipsum passages, and more recently with desktop publishing software like Aldus PageMaker including versions of Lorem Ipsum.</p>
    <p>It is a long established fact that a reader will be distracted by the readable content of a page when looking at its layout. The point of using Lorem Ipsum is that it has a more-or-less normal distribution of letters, as opposed to using 'Content here, content here', making it look like readable English. Many desktop publishing packages and web page editors now use Lorem Ipsum as their default model text, and a search for 'lorem ipsum' will uncover many web sites still in their infancy. Various versions have evolved over the years, sometimes by accident, sometimes on purpose (injected humour and the It is a long established fact that a reader will be distracted by the readable content of a page when looking at its layout. The point of using Lorem Ipsum is that it has a more-or-less normal distribution of letters, as opposed to using 'Content here, content here', making it look like readable English. Many desktop publishing packages and web page editors now use Lorem Ipsum as their default model text, and a search for 'lorem ipsum' will uncover many web sites still in their infancy.</p>
    <p>It is a long established fact that a reader will be distracted by the readable content of a page when looking at its layout. The point of using Lorem Ipsum is that it has a more-or-less normal distribution of letters, as opposed to using 'Content here, content here', making it look like readable English. Many desktop publishing packages and web page editors now use Lorem Ipsum as their default model text, and a search for 'lorem ipsum' will uncover many web sites still in their infancy. Various versions have evolved over the years, sometimes by accident, sometimes on purpose.</p>
  </div>

  <div class="signature" role="img" aria-label="Handwritten signature"></div>
  <div class="letter-body signatory">
    <strong>The Lorem Ipsum</strong><br>
    Sample text for printing and typesetting industry
  </div>

  <div class="footer-rule"></div>
  <div class="footer-contact">555.014.2273<span class="sep">|</span>www.QuillbrookPath.com</div>
  <div class="ownership-tab">Ownership Solutions</div>
</section>

<section class="sheet slide-cover" aria-label="Presentation cover slide">
  <div class="cover-rule"></div>
  <div class="logo-band"><span class="brand">QuillbrookPath</span></div>
  <div class="service-strip">
    <span class="title">Ownership Solutions</span>
    <span class="services"><span>Business Sale</span><span>Acquisition</span><span>Exit Planning</span><span>Valuation</span><span>Growth Engineering</span></span>
  </div>
</section>

<section class="sheet slide-content" aria-label="Presentation content slide">
  <span class="brand">QuillbrookPath</span>
  <div class="header-rule"></div>
  <div class="base-band"></div>
  <div class="contact-tab">555.014.2273<span class="sep">|</span>www.QuillbrookPath.com</div>
</section>

<section class="sheet card-front" aria-label="Business card front">
  <span class="brand">QuillbrookPath</span>
  <div class="card-holder">
    <span class="name">Marcus Dellorane RPA</span>
    <span class="role">Registered Practice Adviser</span>
  </div>
  <ul class="card-contacts">
    <li><svg viewBox="0 0 10 10"><rect width="10" height="10" rx="1.5" fill="#0a3b25"/><rect x="3.2" y="1.8" width="3.6" height="6.4" rx=".6" fill="#fff"/></svg>555.014.2273</li>
    <li><svg viewBox="0 0 10 10"><rect width="10" height="10" rx="1.5" fill="#0a3b25"/><path d="M5 1.6a2.4 2.4 0 0 0-2.4 2.4C2.6 6 5 8.6 5 8.6S7.4 6 7.4 4A2.4 2.4 0 0 0 5 1.6z" fill="#fff"/><circle cx="5" cy="4" r=".9" fill="#0a3b25"/></svg>5678 Harlow Rd. Larkfield, OH 44790</li>
    <li><svg viewBox="0 0 10 10"><rect width="10" height="10" rx="1.5" fill="#0a3b25"/><rect x="2" y="3" width="6" height="4.2" fill="#fff"/><path d="M2 3l3 2.4L8 3" stroke="#0a3b25" stroke-width=".7" fill="none"/></svg>Demo@Quillbrookpath.com</li>
    <li><svg viewBox="0 0 10 10"><rect width="10" height="10" rx="1.5" fill="#0a3b25"/><circle cx="5" cy="5" r="2.8" stroke="#fff" stroke-width=".8" fill="none"/><path d="M2.2 5h5.6M5 2.2c-1.4 1.6-1.4 4 0 5.6M5 2.2c1.4 1.6 1.4 4 0 5.6" stroke="#fff" stroke-width=".6" fill="none"/></svg>www.QuillbrookPath.com</li>
  </ul>
  <div class="card-rule"></div>
  <div class="ownership-tab">Ownership Solutions</div>
</section>

<section class="sheet card-back" aria-label="Business card back">
  <span class="brand">QuillbrookPath</span>
  <div class="service-strip">
    <span class="title">Ownership Solutions</span>
    <span class="services"><span>Business Sale</span><span>Acquisition</span><span>Exit Planning</span><span>Valuation</span><span>Growth Engineering</span></span>
  </div>
</section>

</body>
</html>
```